Business Card

Just need business logo with phone number on it. 0487 312 654
And the following on the bottom of the card.

"Your local plumbing experts".
and emblems for zelpa card, cheque and cash

```html
<!DOCTYPE html>
<html lang="en">
<head>
<meta charset="utf-8">
<title>Ridgeline Plumbing &amp; Drainage – Business Card</title>
<link rel="stylesheet" href="https://fonts.googleapis.com/css2?family=Open+Sans:wght@400;600;700&display=swap">
<style>
  :root {
    --backdrop: #e6e2dd;
    --card: #000000;
    --brand-red: #e8262f;
    --brand-blue: #2a93d5;
    --ink-light: #ffffff;
  }
  * { margin: 0; padding: 0; box-sizing: border-box; }
  html, body {
    width: 1200px;
    height: 1000px;
    overflow: hidden;
    background: var(--backdrop);
    font-family: "Open Sans", Arial, sans-serif;
  }
  .card {
    position: absolute;
    left: 266px;
    width: 666px;
    height: 397px;
    background: var(--card);
    color: var(--ink-light);
    text-align: center;
    overflow: hidden;
  }
  .card--front { top: 74px; }
  .card--back { top: 534px; }

  .brand {
    position: absolute;
    left: 50%;
    display: flex;
    align-items: center;
    gap: 12px;
    white-space: nowrap;
    transform: translate(-50%, -50%);
  }
  .card--front .brand { top: 198px; }
  .card--back .brand { top: 124px; }
  .brand__dot {
    width: 24px;
    height: 24px;
    border-radius: 50%;
    background: var(--brand-blue);
    flex: none;
  }
  .brand__name {
    font-weight: 700;
    font-size: 26px;
    letter-spacing: 1px;
    text-transform: uppercase;
    color: var(--brand-red);
    line-height: 1.1;
  }

  .contact {
    position: absolute;
    top: 210px;
    left: 0;
    right: 0;
  }
  .contact__name {
    font-weight: 700;
    font-size: 21px;
    color: var(--brand-red);
    letter-spacing: 0.5px;
    margin-bottom: 10px;
  }
  .contact__line {
    font-size: 16px;
    line-height: 23px;
  }
  .contact__tagline {
    font-weight: 700;
    font-size: 16px;
    margin-top: 10px;
    line-height: 23px;
  }
  .contact__payment {
    font-size: 16px;
    line-height: 23px;
  }
</style>
</head>
<body>
  <section class="card card--front" aria-label="Card front">
    <div class="brand">
      <span class="brand__dot"></span>
      <span class="brand__name">Ridgeline Plumbing &amp; Drainage</span>
    </div>
  </section>

  <section class="card card--back" aria-label="Card back">
    <div class="brand">
      <span class="brand__dot"></span>
      <span class="brand__name">Ridgeline Plumbing &amp; Drainage</span>
    </div>
    <div class="contact">
      <p class="contact__name">MARCUS DELANEY</p>
      <p class="contact__line">0487 312 654</p>
      <p class="contact__line">info@ridgelineplumbing.com.au</p>
      <p class="contact__tagline">“Your local plumbing experts"</p>
      <p class="contact__payment">Emblems for zelpa card, cheque and cash</p>
    </div>
  </section>
</body>
</html>
```